Stationery Design Project for Nimbora, Chicago

Nimbora, a street parking application which helps car drivers find a street parking spot by offering an ideal path along which to look for parking. This path is calculated by our algorithm based on data (e.g. historical data, baseball games schedule, etc.). Along this path the driver will find a spot and will also save 70% of the search time. Customer we target is reg. between 21 and 45 yo.

We envision something young, fresh, bright and original. Slightly abstract maybe. It should represent the idea and elements of finding street parking in the city, e.g. car(s), parking spot, people, city, etc. (just ideas!).

Logo is attached.

Requirement:
- Business Cards (2 Sided Full Color CMYK)
- Letterhead (1 Sided Full Color CMYK)
- Envelope (1 Sided Full Color CMYK)
- Sticker (1 Sided Full Color CMYK), round with a 2inch diameter.

Reason: We're starting to get more and more designs and need more time to look into all of them. Very exciting!! Thanks to everybody!

Hi all, we're in the process of selecting our favs. Though choices!!! Really good submissions. Will keep you posted and sorry for the delay.

Target Market(s)

Car drivers and owners between 21 and 45

Industry/Entity Type

Parking

Requirements
Must have
• Sticker should be round and include company URL nimbora.com and the new logo which we will attach soon.
Should not have
• Should not be too serious or boring.

```html
<!DOCTYPE html>
<html lang="en">
<head>
<meta charset="utf-8">
<title>Nimbora — Business Card</title>
<link rel="stylesheet" href="https://fonts.googleapis.com/css2?family=Source+Sans+3:wght@400;600;700&display=swap">
<style>
  :root {
    --backdrop: #a9822a;
    --card: #ffffff;
    --ink: #333333;
    --ink-dark: #1c1c1c;
    --brand-blue: #1a8fd6;
    --brand-deep: #1d3f9a;
    --mark-blue: #2456c4;
  }
  * { margin: 0; padding: 0; box-sizing: border-box; }
  html, body { width: 1200px; height: 686px; overflow: hidden; }
  body {
    background: var(--backdrop);
    font-family: "Source Sans 3", "Myriad Pro", Arial, sans-serif;
    color: var(--ink);
    position: relative;
  }
  .card {
    position: absolute;
    width: 524px;
    height: 298px;
    background: var(--card);
  }
  .card--front { left: 55px; top: 157px; }
  .card--back { left: 612px; top: 241px; }

  .brand { position: absolute; display: flex; align-items: center; }
  .brand__dot {
    border-radius: 50%;
    background: radial-gradient(circle at 40% 35%, #4f86e6, var(--mark-blue) 55%, var(--brand-deep));
    flex: none;
  }
  .brand__name {
    font-weight: 600;
    color: var(--ink);
    letter-spacing: 0.5px;
    line-height: 1;
  }
  .card--front .brand { left: 115px; top: 57px; }
  .card--front .brand__dot { width: 82px; height: 82px; margin-right: 12px; }
  .card--front .brand__name { font-size: 46px; }
  .card--back .brand { left: 70px; top: 105px; }
  .card--back .brand__dot { width: 106px; height: 106px; margin-right: 16px; }
  .card--back .brand__name { font-size: 68px; }

  .edge-tab { position: absolute; top: 124px; height: 58px; width: 16px; }
  .edge-tab--left { left: 0; }
  .edge-tab--right { right: 0; }
  .edge-tab__bar {
    position: absolute; top: 0; width: 12px; height: 100%;
    background: linear-gradient(180deg, #2d8fe0, var(--brand-deep));
  }
  .edge-tab__rule { position: absolute; top: 0; width: 3px; height: 100%; background: var(--ink-dark); }
  .edge-tab--left .edge-tab__bar { left: 0; }
  .edge-tab--left .edge-tab__rule { left: 14px; }
  .edge-tab--right .edge-tab__bar { right: 0; }
  .edge-tab--right .edge-tab__rule { right: 14px; }

  .divider {
    position: absolute; left: 194px; top: 163px; width: 124px; height: 2px;
    background: linear-gradient(90deg, rgba(0,0,0,0), #111 45%, rgba(0,0,0,0));
  }

  .contact {
    position: absolute; left: 0; right: 0; top: 184px;
    text-align: center; font-size: 13px; line-height: 21px;
  }
  .contact__person { line-height: 24px; }
  .contact__name { color: var(--brand-blue); font-weight: 700; font-size: 17px; }
  .contact__title { color: var(--ink-dark); font-weight: 700; font-size: 13px; }
  .contact__row { display: flex; justify-content: center; gap: 14px; }
  .contact__item { display: inline-flex; align-items: center; gap: 2px; }
  .contact__item svg { width: 12px; height: 12px; fill: var(--brand-blue); }
</style>
</head>
<body>

<section class="card card--front" aria-label="Business card front">
  <div class="brand">
    <span class="brand__dot"></span>
    <span class="brand__name">Nimbora</span>
  </div>

  <div class="edge-tab edge-tab--left"><span class="edge-tab__bar"></span><span class="edge-tab__rule"></span></div>
  <div class="edge-tab edge-tab--right"><span class="edge-tab__bar"></span><span class="edge-tab__rule"></span></div>

  <div class="divider"></div>

  <div class="contact">
    <p class="contact__person"><span class="contact__name">Your Name</span><span class="contact__title">, Title</span></p>
    <p>Street name City, State, zip code</p>
    <p class="contact__row">
      <span class="contact__item">
        <svg viewBox="0 0 24 24" aria-hidden="true"><path d="M6.6 10.8a15 15 0 0 0 6.6 6.6l2.2-2.2c.3-.3.7-.4 1-.2 1.1.4 2.3.6 3.6.6.6 0 1 .4 1 1V20c0 .6-.4 1-1 1A17 17 0 0 1 3 4c0-.6.4-1 1-1h3.5c.6 0 1 .4 1 1 0 1.3.2 2.5.6 3.6.1.3 0 .7-.2 1z"/></svg>
        123-456-7890
      </span>
      <span class="contact__item">
        <svg viewBox="0 0 24 24" aria-hidden="true"><path d="M6 2h10l2 2v5H6zM3 10h18v8h-3v4H6v-4H3zm5 6v4h8v-4z"/></svg>
        123-456-7890
      </span>
    </p>
    <p class="contact__row">
      <span class="contact__item">
        <svg viewBox="0 0 24 24" aria-hidden="true"><path d="M2 5h20v14H2zm2 2v.5l8 5 8-5V7z"/></svg>
        name@website.com
      </span>
      <span class="contact__item">
        <svg viewBox="0 0 24 24" aria-hidden="true"><path d="M12 2a10 10 0 1 0 0 20 10 10 0 0 0 0-20zm-1 2.1V8H7.6A8 8 0 0 1 11 4.1zm2 0A8 8 0 0 1 16.4 8H13zM4.3 10h6.7v4H4.3a8 8 0 0 1 0-4zm8.7 0h6.7a8 8 0 0 1 0 4H13zm-5.4 6H11v3.9A8 8 0 0 1 7.6 16zm5.4 0h3.4a8 8 0 0 1-3.4 3.9z"/></svg>
        www.website.com
      </span>
    </p>
  </div>
</section>

<section class="card card--back" aria-label="Business card back">
  <div class="brand">
    <span class="brand__dot"></span>
    <span class="brand__name">Nimbora</span>
  </div>
</section>

</body>
</html>
```